Pyschiatry Experts need Marketing Campaign

Ad(s) developed for print advertising sharing our purpose and services, highlighting our medical care providers. Must be welcoming and inviting while displaying a high level of professionalism expected from a physician's office.

Target Market(s)

Local community

Industry/Entity Type

Psychiatry (Healthcare)

Requirements
Must have
• Staff pictures, 'Medication Management Experts', 'Prompt Appointments', 'ADD/ADHD, Bipolar Disorder, Depression, Anxiety, Schizophrenia, Grief Reaction and others' 'Virtual and In-Person Visits'
Nice to have
• Address: 412 E Marlowe Coeur d'Alene Phone (208)555-7193 website: BrightLoftCare.com Hours: Mon - Thur 7am - 6pm

```html
<!DOCTYPE html>
<html lang="en">
<head>
<meta charset="utf-8">
<title>Bright Loft Care – Print Ad</title>
<link href="https://fonts.googleapis.com/css2?family=Montserrat:wght@300;400;500;600;700;800&family=Source+Sans+3:wght@300;400;600&display=swap" rel="stylesheet">
<style>
  :root {
    --teal: #159486;
    --teal-dark: #0f7f73;
    --teal-pale: #cfe9e5;
    --lime: #acd356;
    --lime-text: #8cc03f;
    --ink: #111111;
    --ink-soft: #1b1b1b;
    --navy: #14163a;
    --paper: #ffffff;
    --backdrop: #eef0ed;
    --mustard: #d4a12a;
    --mustard-deep: #b9861a;
    --hair: #3b2a20;
    --studio: #4f5b61;
  }
  * { margin: 0; padding: 0; box-sizing: border-box; }
  html, body { width: 1200px; height: 1200px; overflow: hidden; background: var(--backdrop); }
  body { font-family: "Source Sans 3", sans-serif; color: var(--ink); position: relative; }

  .flyer {
    position: absolute; left: 192px; top: 31px;
    width: 816px; height: 1138px;
    background: var(--paper);
    box-shadow: 0 6px 24px rgba(0,0,0,.18);
    overflow: hidden;
  }
  .abs { position: absolute; }

  /* brand */
  .brand { left: 0; top: 30px; width: 344px; text-align: center; }
  .brand-dot { width: 62px; height: 62px; border-radius: 50%; background: var(--teal); margin: 0 auto 18px; }
  .brand-name {
    font-family: "Montserrat", sans-serif; font-weight: 600; color: var(--teal);
    font-size: 27px; line-height: 30px; letter-spacing: 2px;
  }

  .hero-photo {
    left: 331px; top: 0; width: 485px; height: 556px;
    background:
      radial-gradient(ellipse 38% 24% at 58% 22%, var(--hair) 0%, rgba(59,42,32,.85) 55%, rgba(59,42,32,0) 100%),
      radial-gradient(ellipse 20% 16% at 56% 38%, #a86f4c 0%, rgba(168,111,76,0) 100%),
      radial-gradient(ellipse 55% 38% at 74% 72%, var(--mustard) 0%, var(--mustard-deep) 55%, rgba(185,134,26,0) 100%),
      radial-gradient(ellipse 30% 20% at 95% 98%, #2f3d48 0%, rgba(47,61,72,0) 100%),
      radial-gradient(ellipse 10% 8% at 12% 84%, #9fcf6a 0%, rgba(159,207,106,0) 100%),
      linear-gradient(180deg, #f4f4f2 0%, #ecebe7 55%, #e2e0da 100%);
  }

  .headline {
    left: 69px; top: 216px;
    font-family: "Montserrat", sans-serif; font-weight: 700;
    font-size: 28px; line-height: 33px;
  }
  .services { left: 69px; top: 326px; font-size: 12.5px; line-height: 16px; }

  /* providers */
  .providers-band { left: 0; top: 414px; width: 602px; height: 338px; background: var(--lime); }
  .providers-title {
    left: 26px; top: 432px;
    font-family: "Montserrat", sans-serif; font-size: 21px; line-height: 28px; font-weight: 300; color: var(--ink-soft);
  }
  .providers-title .accent { font-weight: 500; }
  .portrait {
    top: 507px; width: 133px; height: 173px;
    background:
      radial-gradient(ellipse 42% 30% at 50% 40%, #c9a48e 0%, rgba(201,164,142,.6) 55%, rgba(201,164,142,0) 100%),
      radial-gradient(ellipse 70% 25% at 50% 100%, #1f2327 0%, rgba(31,35,39,.7) 60%, rgba(31,35,39,0) 100%),
      radial-gradient(ellipse 80% 70% at 50% 35%, #7b878c 0%, var(--studio) 60%, #2d3337 100%);
  }
  .provider-name { top: 693px; font-size: 12.5px; line-height: 16px; color: var(--ink-soft); }

  .highlights { left: 602px; top: 556px; width: 214px; height: 196px; background: var(--teal); }
  .highlights ul { list-style: none; padding: 19px 0 0 12px; width: 198px; color: #fff; font-size: 12.4px; line-height: 18.3px; }
  .highlights li { position: relative; padding-left: 9px; }
  .highlights li::before { content: ""; position: absolute; left: 0; top: 7px; width: 4px; height: 4px; border-radius: 50%; background: var(--lime); }

  /* migraine */
  .migraine-title {
    left: 52px; top: 760px;
    font-family: "Montserrat", sans-serif; font-size: 21px; line-height: 28px; font-weight: 400; color: var(--ink-soft);
  }
  .migraine-text { left: 231px; top: 771px; width: 535px; font-size: 12.2px; line-height: 17px; }

  .physician-band { left: 0; top: 863px; width: 577px; height: 141px; background: var(--teal); }
  .physician-photo {
    left: 41px; top: 863px; width: 109px; height: 141px;
    background:
      radial-gradient(ellipse 38% 30% at 50% 42%, #d8a58a 0%, rgba(216,165,138,.5) 60%, rgba(216,165,138,0) 100%),
      radial-gradient(ellipse 80% 28% at 50% 100%, #e9e2d4 0%, rgba(233,226,212,0) 100%),
      linear-gradient(180deg, #7a5a3c 0%, #a07a58 50%, #c9b8a2 100%);
  }
  .physician-text { left: 174px; top: 903px; width: 372px; color: #fff; font-size: 13.6px; line-height: 19.6px; }

  .head-icons {
    left: 612px; top: 849px; width: 162px; height: 152px; border-radius: 10px;
    background:
      radial-gradient(circle at 30% 48%, rgba(21,148,134,.35) 0%, rgba(21,148,134,0) 38%),
      radial-gradient(circle at 88% 14%, rgba(21,148,134,.3) 0%, rgba(21,148,134,0) 16%),
      radial-gradient(circle at 80% 56%, rgba(21,148,134,.3) 0%, rgba(21,148,134,0) 16%),
      radial-gradient(circle at 46% 92%, rgba(21,148,134,.3) 0%, rgba(21,148,134,0) 16%),
      var(--paper);
  }

  /* contact */
  .contact-line { left: 90px; font-family: "Montserrat", sans-serif; font-size: 23px; line-height: 28px; color: var(--ink-soft); }
  .contact-icon { left: 52px; width: 26px; height: 26px; }
  .booking { left: 549px; top: 1030px; }
  .booking-label { font-family: "Montserrat", sans-serif; font-weight: 700; color: var(--lime-text); font-size: 13.5px; line-height: 18px; }
  .booking-phone { font-family: "Montserrat", sans-serif; font-weight: 800; color: var(--navy); font-size: 21px; line-height: 24px; letter-spacing: .5px; }
  .booking-hours { font-family: Arial, sans-serif; font-size: 13px; line-height: 18px; margin-top: 2px; }
  .calendar-icon { left: 495px; top: 1031px; width: 36px; height: 36px; }
</style>
</head>
<body>
<div class="flyer">

  <div class="abs brand">
    <div class="brand-dot"></div>
    <div class="brand-name">BRIGHT LOFT<br>CARE</div>
  </div>

  <div class="abs hero-photo" role="img" aria-label="Photo of a smiling woman with curly hair in a mustard top, seated in a bright room with a plant"></div>

  <h1 class="abs headline">Helping Bodies<br>Helping Minds<br>Helping You</h1>
  <p class="abs services">Mental Health and Psychiatry Services<br>Migraine and Neurospasticity Intervention</p>

  <div class="abs providers-band"></div>
  <h2 class="abs providers-title">Meet Our <span class="accent">Mental<br>Health Providers</span></h2>

  <div class="abs portrait" style="left:19px" role="img" aria-label="Studio portrait of Owen Marsh"></div>
  <div class="abs portrait" style="left:160px" role="img" aria-label="Studio portrait of Dana Whitfield"></div>
  <div class="abs portrait" style="left:301px" role="img" aria-label="Studio portrait of Owen Marsh"></div>
  <div class="abs portrait" style="left:442px" role="img" aria-label="Studio portrait of Ruth Calloway"></div>

  <p class="abs provider-name" style="left:28px">Owen Marsh<br>PMHNP - BC</p>
  <p class="abs provider-name" style="left:160px">Dana Whitfield,<br>PMHNP - BC</p>
  <p class="abs provider-name" style="left:300px">Owen Marsh<br>PMHNP - BC</p>
  <p class="abs provider-name" style="left:445px">Ruth Calloway,<br>PMHNP-BC, DNP</p>

  <div class="abs highlights">
    <ul>
      <li>Medication Management Experts.</li>
      <li>Prompt Appointments', 'ADD/ADHD, Bipolar Disorder, Depression, Anxiety, Schizophrenia, Grief Reaction and others.</li>
      <li>Virtual and In-Person Visits.</li>
    </ul>
  </div>

  <h2 class="abs migraine-title">Migraine and<br>Neurospasticity<br>Intervention</h2>
  <p class="abs migraine-text">Migraine management and intervention can be a complex journey. Identifying food and environmental triggers, identification of migraine type, pharmacological management with a new generation of highly effective medications and/or botulinum injections are all part of our comprehensive care program for migraine sufferers.</p>

  <div class="abs physician-band"></div>
  <div class="abs physician-photo" role="img" aria-label="Portrait of Dr. Alan Pruitt in front of a wood wall"></div>
  <p class="abs physician-text">A board certified family practice physician, Dr. Alan Pruitt has incorporated migraine management and botulinum toxin injections into his practice for several years.</p>

  <div class="abs head-icons" role="img" aria-label="Teal line illustrations of one large and three small heads with brains"></div>

  <svg class="abs contact-icon" style="top:1038px" viewBox="0 0 26 26" aria-hidden="true">
    <circle cx="13" cy="13" r="12" fill="var(--teal)"/>
    <path d="M13 6a5 5 0 0 0-5 5c0 4 5 9 5 9s5-5 5-9a5 5 0 0 0-5-5z" fill="#fff"/>
    <circle cx="13" cy="11" r="2" fill="var(--teal)"/>
  </svg>
  <p class="abs contact-line" style="top:1037px">412 E Marlowe Coeur d'Alene</p>

  <svg class="abs contact-icon" style="top:1074px" viewBox="0 0 26 26" aria-hidden="true">
    <circle cx="13" cy="13" r="12" fill="var(--teal)"/>
    <circle cx="13" cy="13" r="7" fill="none" stroke="#fff" stroke-width="1.5"/>
    <ellipse cx="13" cy="13" rx="3" ry="7" fill="none" stroke="#fff" stroke-width="1.3"/>
    <line x1="6" y1="13" x2="20" y2="13" stroke="#fff" stroke-width="1.3"/>
  </svg>
  <p class="abs contact-line" style="top:1073px">BrightLoftCare.com</p>

  <svg class="abs calendar-icon" viewBox="0 0 36 36" aria-hidden="true">
    <rect x="2" y="6" width="32" height="27" rx="2" fill="none" stroke="var(--teal)" stroke-width="3"/>
    <rect x="2" y="6" width="32" height="7" fill="var(--teal)"/>
    <rect x="9" y="2" width="3" height="8" fill="var(--teal)"/>
    <rect x="24" y="2" width="3" height="8" fill="var(--teal)"/>
    <path d="M18 18v10M13 23h10" stroke="var(--teal)" stroke-width="3"/>
  </svg>
  <div class="abs booking">
    <div class="booking-label">Book an Appointment</div>
    <div class="booking-phone">(208)555-7193</div>
    <div class="booking-hours">Mon - Thur 7am - 6pm</div>
  </div>

</div>
</body>
</html>
```